Falkrin homes and renovations business card design.

Would like some new card designs utilizing my new logo that look professional. I am open to different colors on the logo or utilize the same ones we have. I like the original concept but would like to see some fresh ideas and build on what we have already done.

Target Market(s)

Custom home building industry, Real estate sales, Renovation projects.

Industry/Entity Type

Home Builder

Contact Information for Business Card

Falkrin Homes and Renovations
2871 96th Avenue
Halvorne, Northaven
T2R3W8
Home : 403- 718-4063 Cell: 403- 294-5170

My info is : Dax Falkrin, President and CEO
email: falkrinhomes@maildrop-example.net
Website: falkrinhomes-example.com
websit

Requirements
Must have
• Must Use my new logo design. I am open to different colors on the logo or utilize the same ones in the existing design. I can upload the original logo design if needed.

```html
<!DOCTYPE html>
<html lang="en">
<head>
<meta charset="utf-8">
<title>Falkrin Homes and Renovations – Business Card</title>
<link rel="stylesheet" href="https://fonts.googleapis.com/css2?family=Montserrat:wght@400;500;600;700&display=swap">
<style>
  :root {
    --backdrop: #2b2b2b;
    --card-dark: #050505;
    --card-light: #ffffff;
    --gold: #a97d2c;
    --gold-bright: #f0b424;
    --grey-text: #8a8a8a;
    --white-text: #f2f2f2;
  }
  * { margin: 0; padding: 0; box-sizing: border-box; }
  html, body {
    width: 1200px; height: 864px; overflow: hidden;
    background: var(--backdrop);
    font-family: "Montserrat", sans-serif;
  }
  .sheet {
    width: 1200px; height: 864px;
    display: flex; align-items: center; justify-content: center; gap: 40px;
  }
  .card {
    width: 540px; height: 309px;
    position: relative;
    box-shadow: 0 10px 24px rgba(0,0,0,.45);
  }
  .card--back {
    background: var(--card-dark);
    display: flex; flex-direction: column; align-items: center; justify-content: center;
  }
  .brand {
    display: flex; align-items: center; gap: 10px;
    color: var(--gold); font-weight: 700;
  }
  .brand__mark { width: 14px; height: 14px; background: var(--gold); flex: none; }
  .card--back .brand { font-size: 25px; }
  .card--back .brand-name { max-width: 300px; line-height: 1.15; }
  .back-url {
    margin-top: 44px; color: var(--white-text);
    font-size: 13px; letter-spacing: .3px;
  }
  .card--front {
    background: var(--card-light);
    display: flex; align-items: center;
    padding: 0 24px 0 30px;
  }
  .card--front .brand { font-size: 19px; width: 180px; line-height: 1.15; flex: none; }
  .divider {
    width: 1.5px; height: 150px; background: var(--gold);
    margin: 0 18px 0 16px; flex: none;
  }
  .details { color: var(--grey-text); font-size: 11px; line-height: 1.45; white-space: nowrap; }
  .person-name { color: var(--gold); font-weight: 700; font-size: 17px; line-height: 1.15; }
  .person-role { font-size: 12px; margin-bottom: 10px; }
  .address { margin-bottom: 8px; font-size: 11.5px; }
  .contact-list { list-style: none; }
  .contact-list li { display: flex; align-items: center; gap: 7px; }
  .contact-list svg { width: 11px; height: 11px; flex: none; fill: var(--gold-bright); }
</style>
</head>
<body>
<main class="sheet">
  <section class="card card--back" aria-label="Card back">
    <div class="brand">
      <span class="brand__mark"></span>
      <span class="brand-name">Falkrin Homes and Renovations</span>
    </div>
    <p class="back-url">www.falkrinhomes-example.com</p>
  </section>

  <section class="card card--front" aria-label="Card front">
    <div class="brand">
      <span class="brand__mark"></span>
      <span class="brand-name">Falkrin Homes and Renovations</span>
    </div>
    <div class="divider"></div>
    <div class="details">
      <p class="person-name">Dax Falkrin</p>
      <p class="person-role">President and CEO</p>
      <p class="address">2871 96th Avenue<br>Halvorne, Northaven, T2R3W8</p>
      <ul class="contact-list">
        <li><svg viewBox="0 0 12 12" aria-hidden="true"><path d="M2.5 1l2 2-1 1.5c.7 1.5 2 2.8 3.5 3.5L8.5 7l2 2-1.5 2C5 10.5 1.5 7 1 3z"/></svg>403- 718-4063</li>
        <li><svg viewBox="0 0 12 12" aria-hidden="true"><path d="M3.5 0.5h5v11h-5zM4.5 1.5v8h3v-8z" fill-rule="evenodd"/></svg>403- 294-5170</li>
        <li><svg viewBox="0 0 12 12" aria-hidden="true"><path d="M1 2.5h10v7H1zM1.5 3l4.5 3.5L10.5 3z"/></svg>falkrinhomes@maildrop-example.net</li>
        <li><svg viewBox="0 0 12 12" aria-hidden="true"><path d="M6 .5a5.5 5.5 0 1 0 0 11A5.5 5.5 0 0 0 6 .5zm0 1c.7.8 1.2 2 1.3 3.5H4.7C4.8 3.5 5.3 2.3 6 1.5zM1.6 6h2.1c.1 1.6.6 2.9 1.2 3.8A4.5 4.5 0 0 1 1.6 6zm6.7 0h2.1a4.5 4.5 0 0 1-3.3 3.8c.6-.9 1.1-2.2 1.2-3.8zM4.7 6h2.6C7.2 7.5 6.7 8.7 6 9.5 5.3 8.7 4.8 7.5 4.7 6z"/></svg>falkrinhomes-example.com</li>
      </ul>
    </div>
  </section>
</main>
</body>
</html>
```